KBT Business Cards

We require business cards for our business. We would like a matte black back to the card, with our logo centred in the middle. The front side of the card is open to design.

Target Market(s)

Clients looking for legal services (professional)

Industry/Entity Type

Legal

Contact Information for Business Card

Doran Kelbrath
Partner
Mobile: 0461 738 524
Email: doran@kbtlaw.co
Website: www.kbtlaw.co
Level 3, 118 Wendmore Street
Sydney NSW 2000

Font styles to use
Other font styles liked:
• Avenir

Colors
f04a50
ffffff
1b1b1b

Requirements
Must have
• Black back with logo included in the centre of the card.
• Our font is Avenir.

```html
<!DOCTYPE html>
<html lang="en">
<head>
<meta charset="utf-8">
<title>KBT Legal Business Cards</title>
<link rel="stylesheet" href="https://fonts.googleapis.com/css2?family=Roboto:wght@400;500;700&display=swap">
<style>
  :root {
    --backdrop: #e4e4e4;
    --paper: #ffffff;
    --ink: #231f20;
    --ink-soft: #5a5a5a;
    --accent: #d6264a;
    --accent-deep: #a31d3a;
    --rule: #d8d8d8;
    --on-dark: #ffffff;
  }
  * { margin: 0; padding: 0; box-sizing: border-box; }
  html, body {
    width: 1125px; height: 1200px; overflow: hidden;
    background: var(--backdrop);
    font-family: "Roboto", Arial, sans-serif;
  }
  .card {
    position: absolute; left: 170px; width: 800px; height: 457px;
    overflow: hidden;
    box-shadow: 0 3px 10px rgba(0,0,0,0.25);
  }
  .card--front { top: 106px; background: var(--paper); }
  .card--back  { top: 638px; background: var(--ink); }

  /* Front */
  .brand { position: absolute; left: 92px; top: 202px; display: flex; align-items: center; gap: 16px; }
  .brand__mark { width: 36px; height: 36px; background: var(--accent); }
  .brand__name { font-size: 30px; font-weight: 500; color: var(--ink); letter-spacing: 0.5px; white-space: nowrap; }

  .divider { position: absolute; left: 402px; top: 132px; width: 1px; height: 196px; background: var(--rule); }

  .contact { position: absolute; left: 431px; top: 134px; }
  .contact__name { font-size: 29px; font-weight: 700; color: var(--accent); line-height: 1.1; }
  .contact__role { font-size: 19px; font-weight: 500; color: var(--ink); margin-top: 2px; }
  .contact__address { font-size: 18.5px; color: var(--ink-soft); line-height: 25px; margin-top: 14px; }
  .contact__lines { margin-top: 14px; list-style: none; }
  .contact__line { display: flex; align-items: center; gap: 13px; font-size: 18.5px; color: var(--ink-soft); line-height: 27px; }
  .contact__icon { width: 17px; height: 17px; flex: none; }

  .footer-band {
    position: absolute; left: 0; bottom: 0; width: 312px; height: 41px;
    background: var(--ink);
    clip-path: polygon(0 0, 284px 0, 312px 100%, 0 100%);
  }
  .footer-band__url {
    position: absolute; left: 40px; top: 9px;
    font-size: 18px; color: var(--on-dark); letter-spacing: 5.6px;
  }
  .footer-rule {
    position: absolute; left: 310px; right: 0; bottom: 12px; height: 7px;
    background: linear-gradient(90deg, var(--accent-deep), var(--accent));
    box-shadow: 0 2px 0 #d0d0d0;
  }

  /* Back: logo centred */
  .card--back { display: flex; align-items: center; justify-content: center; }
  .back-brand { display: flex; align-items: center; gap: 26px; }
  .back-brand__mark { width: 64px; height: 64px; background: var(--accent); }
  .back-brand__name { font-size: 56px; font-weight: 500; color: var(--on-dark); letter-spacing: 1px; line-height: 1; white-space: nowrap; }
</style>
</head>
<body>
  <section class="card card--front" aria-label="Card front">
    <div class="brand">
      <span class="brand__mark"></span>
      <span class="brand__name">KBT LEGAL</span>
    </div>
    <div class="divider"></div>
    <div class="contact">
      <h1 class="contact__name">Doran Kelbrath</h1>
      <p class="contact__role">Partner</p>
      <p class="contact__address">Level 3, 118 Wendmore Street<br>Sydney NSW 2000</p>
      <ul class="contact__lines">
        <li class="contact__line">
          <svg class="contact__icon" viewBox="0 0 17 17" aria-hidden="true">
            <rect x="3.5" y="0.8" width="10" height="15.4" rx="1.5" fill="none" stroke="#d6264a" stroke-width="1.6"/>
            <rect x="5.5" y="12.2" width="6" height="1.4" fill="#d6264a"/>
          </svg>
          <span>0461 738 524</span>
        </li>
        <li class="contact__line">
          <svg class="contact__icon" viewBox="0 0 17 17" aria-hidden="true">
            <rect x="0.5" y="4" width="16" height="10" fill="#d6264a"/>
            <path d="M0.5 4 L8.5 10 L16.5 4" fill="none" stroke="#fff" stroke-width="1.2"/>
          </svg>
          <span>doran@kbtlaw.co</span>
        </li>
      </ul>
    </div>
    <div class="footer-band"><span class="footer-band__url">www.kbtlaw.co</span></div>
    <div class="footer-rule"></div>
  </section>

  <section class="card card--back" aria-label="Card back">
    <div class="back-brand">
      <span class="back-brand__mark"></span>
      <span class="back-brand__name">KBT LEGAL</span>
    </div>
  </section>
</body>
</html>
```